business card for a massage therapy practice named 'Cedar and Willow Massage Studio'

I really need a trendy, yet easy on the eyes business card to complement my logo. Ideally with some gold or rose gold foil work.

My uploaded file of the logo I have in horizontal but I have a vertical version as well. Another color that is used in the website is a blush pink here and there. I'd like to see some trendy tropical leaves in the design.

```html
<!DOCTYPE html>
<html lang="en">
<head>
<meta charset="utf-8">
<title>Cedar and Willow Massage Studio – Business Card</title>
<link rel="stylesheet" href="https://fonts.googleapis.com/css2?family=Roboto:wght@400;500;700&family=Dancing+Script:wght@600&display=swap">
<style>
  :root {
    --ink: #1c1c1c;
    --gold: #b59a6a;
    --mint: #7fd1bd;
    --teal-box: #8fd3c1;
    --blush: #f3c9dc;
    --rose: #e6a3bd;
    --forest: #0b211d;
    --leaf: #1f4b3e;
    --paper: #ffffff;
    --muted: #3a3a3a;
  }
  * { box-sizing: border-box; margin: 0; padding: 0; }
  html, body { width: 1200px; height: 1040px; overflow: hidden; background: var(--paper); }
  body { font-family: "Roboto", Arial, sans-serif; color: var(--ink); position: relative; }

  /* Brand lockup */
  .brand-lockup { position: absolute; left: 380px; top: 50px; display: flex; align-items: center; gap: 18px; }
  .brand-mark { width: 74px; height: 150px; }
  .brand-name { font-size: 52px; font-weight: 500; color: var(--ink); line-height: 1; }
  .brand-sub { font-size: 30px; font-weight: 500; color: var(--mint); letter-spacing: 6px; margin-top: 14px; text-transform: uppercase; }

  .card { position: absolute; width: 540px; height: 318px; box-shadow: 0 10px 28px rgba(0,0,0,.22); overflow: hidden; }

  /* Front */
  .card-front { left: 40px; top: 390px; }
  .front-pattern { position: absolute; inset: 0; }
  .front-logo { position: absolute; left: 0; right: 0; top: 112px; display: flex; justify-content: center; align-items: center; gap: 14px; color: var(--rose); }
  .front-logo .mark { width: 40px; height: 90px; }
  .front-logo .name { font-size: 38px; font-weight: 500; line-height: 1; }
  .front-logo .sub { font-size: 20px; letter-spacing: 4px; margin-top: 10px; text-transform: uppercase; }
  .front-handle { position: absolute; left: 0; right: 0; bottom: 24px; display: flex; justify-content: center; align-items: center; gap: 8px; color: #fff; font-size: 15px; }
  .dot { width: 12px; height: 12px; border-radius: 50%; background: currentColor; display: inline-block; }

  /* Back */
  .card-back { left: 620px; top: 390px; background: var(--paper); }
  .back-top { position: relative; height: 190px; padding: 22px 22px 0 22px; }
  .back-logo { display: flex; align-items: center; gap: 8px; }
  .back-logo .mark { width: 24px; height: 56px; }
  .back-logo .name { font-size: 20px; font-weight: 500; }
  .back-logo .sub { font-size: 11px; letter-spacing: 2px; color: var(--mint); margin-top: 4px; text-transform: uppercase; }
  .holder { position: absolute; right: 22px; top: 28px; text-align: right; font-size: 15px; line-height: 20px; color: var(--muted); }
  .holder strong { font-weight: 700; color: var(--ink); display: block; }
  .sessions-title { font-family: "Dancing Script", cursive; color: var(--mint); font-size: 20px; margin-top: 14px; }
  .sessions { list-style: none; display: grid; grid-template-columns: 242px 1fr; font-size: 14px; line-height: 19px; color: var(--muted); margin-top: 4px; }
  .sessions li { display: flex; align-items: center; gap: 8px; white-space: nowrap; }
  .sessions li::before { content: ""; width: 9px; height: 6px; border-radius: 50%; background: var(--rose); transform: rotate(-25deg); }
  .back-band { position: absolute; left: 0; right: 0; bottom: 0; height: 128px; background: var(--blush); padding: 14px 22px; }
  .contact { list-style: none; font-size: 16px; line-height: 22.5px; }
  .contact li { display: flex; align-items: center; gap: 12px; white-space: nowrap; }
  .contact svg { width: 15px; height: 15px; flex: none; }
  .cta { position: absolute; right: 22px; top: 18px; width: 178px; border: 3px solid var(--paper); white-space: nowrap; }
  .cta-label { background: var(--paper); font-size: 15px; font-weight: 500; padding: 6px 10px; }
  .cta-phone { background: var(--teal-box); font-size: 17px; font-weight: 700; padding: 7px 10px; display: flex; align-items: center; gap: 8px; }
  .cta-phone svg { flex: none; }
</style>
</head>
<body>

<header class="brand-lockup">
  <svg class="brand-mark" role="img" aria-label="Gold pineapple illustration"><rect width="74" height="150" rx="30" fill="var(--gold)" opacity=".75"/></svg>
  <div>
    <div class="brand-name">Cedar and Willow</div>
    <div class="brand-sub">Massage Studio</div>
  </div>
</header>

<section class="card card-front">
  <svg class="front-pattern" width="540" height="318" role="img" aria-label="Tropical leaves and lilies pattern on dark green">
    <defs>
      <radialGradient id="jungle" cx="50%" cy="50%" r="70%">
        <stop offset="35%" stop-color="var(--forest)"/>
        <stop offset="100%" stop-color="var(--leaf)"/>
      </radialGradient>
    </defs>
    <rect width="540" height="318" fill="url(#jungle)"/>
  </svg>
  <div class="front-logo">
    <svg class="mark" role="img" aria-label="Rose gold pineapple illustration"><rect width="40" height="90" rx="16" fill="var(--rose)" opacity=".8"/></svg>
    <div>
      <div class="name">Cedar and Willow</div>
      <div class="sub">Massage Studio</div>
    </div>
  </div>
  <div class="front-handle"><span class="dot"></span> / @cedarandwillow</div>
</section>

<section class="card card-back">
  <div class="back-top">
    <div class="back-logo">
      <svg class="mark" role="img" aria-label="Gold pineapple illustration"><rect width="24" height="56" rx="10" fill="var(--gold)" opacity=".75"/></svg>
      <div>
        <div class="name">Cedar and Willow</div>
        <div class="sub">Massage Studio</div>
      </div>
    </div>
    <div class="holder"><strong>Dana Whitlock LMT</strong>555.201.4837</div>
    <div class="sessions-title">Our Most Popular Sessions</div>
    <ul class="sessions">
      <li>Clinical Bodywork</li>
      <li>Lymphatic Drainage Massage</li>
      <li>Therapeutic Massage</li>
      <li>Sacramento Sinus Facial</li>
      <li>Integrated Hot Stone Massage</li>
      <li>Australian Foot Treatment</li>
    </ul>
  </div>
  <div class="back-band">
    <ul class="contact">
      <li><svg viewBox="0 0 16 16"><rect x="1" y="3" width="14" height="10" fill="var(--ink)"/><path d="M1 3l7 6 7-6" stroke="var(--blush)" stroke-width="1.5" fill="none"/></svg>hello@cedarandwillow.com</li>
      <li><svg viewBox="0 0 16 16"><rect x="3" y="3" width="10" height="7" fill="none" stroke="var(--ink)" stroke-width="1.6"/><rect x="1" y="11" width="14" height="2" fill="var(--ink)"/></svg>www.cedarandwillow.com</li>
      <li><svg viewBox="0 0 16 16"><circle cx="8" cy="8" r="6" fill="var(--ink)"/></svg>/ @cedarandwillow</li>
      <li><svg viewBox="0 0 16 16"><circle cx="8" cy="8" r="6" fill="var(--ink)"/></svg>/ @cedarandwillow</li>
    </ul>
    <div class="cta">
      <div class="cta-label">Call for Appointment</div>
      <div class="cta-phone">
        <svg width="14" height="14" viewBox="0 0 16 16"><path d="M4 1l3 3-2 2c1 2 3 4 5 5l2-2 3 3-2 3C7 14 2 9 1 3z" fill="var(--ink)"/></svg>
        <span>(555) 201-4837</span>
      </div>
    </div>
  </div>
</section>

</body>
</html>
```